NZ First of it's kind solutions directory and marketplace for busy Mums needs a business card design

We need a business card design for our new nationwide business in NZ (long term plans to go global). We provide solutions to the everyday challenges that busy Mums face by connecting them with quality communities and suppliers of carefully selected, relevant products and services. We sell direct via our online marketplace. The final design should communicate our values of inclusivity, quality and smart solutions. Colours should incorporate our logo colour palette of #477077 and #6ba8b2. Our website is at https://www.brightnestmums.example

Target Market(s)

busy Mums, Age 28 – 50, female, income over $100K, location main centres NZ primarily but NZ wide. Is likely juggling work or career with a young family. Probably had hobbies which have fallen by the wayside.
-Wants to succeed in her chosen career without compromising on family life
-to successfully juggle her career without feeling like she is compromising her children
- Is time poor, something always has to give and it’s generally her health (she’ll stay up late, get stressed)
- probably ex corporate or professional career. Has discretional income

Industry/Entity Type

Business

Contact Information for Business Card

Lena Forbisher, Founder, BrightNestMums.example (Strapline Tap; Gather; Sorted), 47 Kowhai Terrace, Ellerslie, Auckland 1051, New Zealand. Mob: 021 483 517 Ph: +64 (0)9 571 4860

Font styles to use
Other font styles liked:
• Raleway, and/or Architects Daughter

Colors
00a990
33b8a4
86cfc6
cfeae6

Requirements
Must have
• the above details, streamline. the logo and colours associated with those logos
Should not have
• foil or metallic colours

```html
<!DOCTYPE html>
<html lang="en">
<head>
<meta charset="utf-8">
<title>BrightNestMums Business Card</title>
<link rel="stylesheet" href="https://fonts.googleapis.com/css2?family=Baloo+2:wght@700&family=Roboto:ital,wght@0,400;1,400&display=swap">
<style>
  :root {
    --brand-dark: #3a5a61;
    --brand-mid: #477077;
    --brand-light: #6ba8b2;
    --ink: #3b3d40;
    --card: #f7f7f6;
    --backdrop: #e4e4e4;
  }
  * { box-sizing: border-box; margin: 0; padding: 0; }
  html, body { width: 1200px; height: 576px; overflow: hidden; }
  body {
    position: relative;
    background: var(--backdrop);
    font-family: "Roboto", Arial, sans-serif;
    color: var(--ink);
  }
  .card {
    position: absolute;
    top: 138px;
    width: 484px;
    height: 294px;
    background: var(--card);
    border-radius: 12px;
    overflow: hidden;
    box-shadow: 0 2px 6px rgba(0,0,0,0.18);
  }
  .card--front { left: 82px; }
  .card--back { left: 602px; width: 480px; height: 292px; }

  .brand-mark {
    display: inline-block;
    width: 30px; height: 30px;
    border-radius: 50%;
    background: var(--brand-mid);
    flex: none;
  }
  .brand-name {
    font-family: "Baloo 2", "Roboto", sans-serif;
    font-weight: 700;
    color: var(--brand-mid);
    letter-spacing: -0.3px;
    line-height: 1;
    white-space: nowrap;
  }
  .strapline {
    font-size: 9.5px;
    letter-spacing: 3px;
    color: var(--ink);
    text-transform: uppercase;
    white-space: nowrap;
  }
  .strapline .sep { color: var(--brand-light); margin: 0 4px; }

  /* front */
  .front-logo {
    position: absolute;
    left: 34px; top: 128px;
    display: flex; align-items: center; gap: 8px;
  }
  .front-logo .brand-name { font-size: 24px; }
  .card--front .strapline { position: absolute; left: 74px; top: 163px; }
  .front-feature {
    position: absolute;
    left: 286px; top: 18px;
    width: 198px; height: 276px;
    background: linear-gradient(160deg, var(--brand-light) 0%, var(--brand-mid) 45%, var(--brand-dark) 100%);
    border-top-left-radius: 100px;
  }

  /* back */
  .back-logo {
    position: absolute;
    left: 30px; top: 70px;
    width: 220px;
    display: flex; flex-direction: column; align-items: center;
  }
  .back-logo .brand-mark { width: 46px; height: 46px; margin-bottom: 26px; }
  .back-logo .brand-name { font-size: 25px; }
  .back-logo .strapline { margin-top: 8px; }

  .contact { position: absolute; left: 268px; top: 52px; }
  .contact__name {
    font-family: "Baloo 2", "Roboto", sans-serif;
    font-weight: 700;
    font-size: 21px;
    color: var(--brand-dark);
    line-height: 1.1;
  }
  .contact__role { font-style: italic; font-size: 12.5px; margin-top: 2px; }
  .contact__address { font-size: 12.5px; line-height: 18px; margin-top: 18px; }
  .contact__list { list-style: none; margin-top: 14px; font-size: 12.5px; }
  .contact__list li { display: flex; align-items: center; gap: 8px; height: 18px; white-space: nowrap; }
  .contact__list svg { width: 12px; height: 12px; fill: var(--brand-mid); flex: none; }

  .footer-line {
    position: absolute; left: 0; bottom: 4px;
    width: 240px; height: 8px;
    background: var(--brand-light);
  }
  .footer-band {
    position: absolute; right: 0; bottom: 0;
    width: 260px; height: 36px;
    background: var(--brand-dark);
    clip-path: polygon(18px 0, 100% 0, 100% 100%, 0 100%);
    border-top-left-radius: 8px;
  }
  .footer-web {
    position: absolute; left: 269px; bottom: 11px;
    font-size: 12.5px; color: #ffffff;
  }
</style>
</head>
<body>
  <section class="card card--front">
    <div class="front-logo">
      <span class="brand-mark"></span>
      <span class="brand-name">BrightNestMums</span>
    </div>
    <p class="strapline">Tap<span class="sep">|</span>Gather<span class="sep">|</span>Sorted</p>
    <div class="front-feature" role="img" aria-label="Large brand decoration in teal tones"></div>
  </section>

  <section class="card card--back">
    <div class="back-logo">
      <span class="brand-mark"></span>
      <span class="brand-name">BrightNestMums</span>
      <p class="strapline">Tap<span class="sep">|</span>Gather<span class="sep">|</span>Sorted</p>
    </div>

    <div class="contact">
      <h1 class="contact__name">Lena Forbisher</h1>
      <p class="contact__role">Founder</p>
      <p class="contact__address">47 Kowhai Terrace, Ellerslie,<br>Auckland 1051, New Zealand</p>
      <ul class="contact__list">
        <li>
          <svg viewBox="0 0 12 12" aria-hidden="true"><path d="M3 0h6a1 1 0 0 1 1 1v10a1 1 0 0 1-1 1H3a1 1 0 0 1-1-1V1a1 1 0 0 1 1-1zm0 1.5v7.5h6V1.5zm3 8.3a.7.7 0 1 0 0 1.4.7.7 0 0 0 0-1.4z"/></svg>
          021 483 517
        </li>
        <li>
          <svg viewBox="0 0 12 12" aria-hidden="true"><path d="M1 3.5C1 2 3 1.5 6 1.5S11 2 11 3.5V5H8.5V4h-5v1H1zM2.5 6h7L11 11H1zm3.5 1.2a1.6 1.6 0 1 0 0 3.2 1.6 1.6 0 0 0 0-3.2z"/></svg>
          +64 (0)9 571 4860
        </li>
        <li>
          <svg viewBox="0 0 12 12" aria-hidden="true"><path d="M0 2h12v8H0zm1 1v.3l5 3.2 5-3.2V3zm0 1.5V9h10V4.5L6 7.7z"/></svg>
          lena@brightnestmums.example
        </li>
      </ul>
    </div>

    <div class="footer-line"></div>
    <div class="footer-band"></div>
    <p class="footer-web">www.BrightNestMums.example</p>
  </section>
</body>
</html>
```